Automotive eCommerce Business looking for a business card design

Looking for a clean and simple business card design. Our company name is "Brindle Auto" and we are a company specializing in the ecommerce sales of automotive parts, specifically for pick up trucks and large SUVs. Our company colours are red, black, and white.

Feel free to use the logo provided or create a new logo that you seem fit. Looking forward to your creative ideas!

Industry/Entity Type

Automotive

Contact Information for Business Card

We were thinking of a possibly two-sided design featuring just the logo and company name on one side, and personal information on the other side. Single sided designs will be considered as well.

Font styles to use
Serif
Sans Serif
Decorative

Colors
ec1f27
ffffff
000000

Requirements
Must have
• Space for employee's name, title, phone number and email address, along with the company address and website somewhere.

```html
<!DOCTYPE html>
<html lang="en">
<head>
<meta charset="utf-8">
<title>Brindle Auto Ltd. – Business Card</title>
<link rel="stylesheet" href="https://fonts.googleapis.com/css2?family=Cinzel:wght@500&family=Roboto:wght@400&family=Roboto+Condensed:wght@500&display=swap">
<style>
  :root {
    --backdrop: #2b2b2b;
    --card-red: #9b1c20;
    --band-grey: #555555;
    --paper: #f1f1f1;
    --ink-white: #ffffff;
    --ink-grey: #4a4a4a;
  }
  * { margin: 0; padding: 0; box-sizing: border-box; }
  html, body { width: 1200px; height: 960px; overflow: hidden; }
  body { background: var(--backdrop); position: relative; }

  .card { position: absolute; width: 600px; height: 342px; overflow: hidden; }

  /* Front side */
  .card-front { left: 314px; top: 113px; background: var(--card-red); color: var(--ink-white); }
  .card-front .side-band {
    position: absolute; right: 0; top: 0; width: 154px; height: 100%;
    background: linear-gradient(135deg, #666 0%, var(--band-grey) 100%);
  }
  .company-name {
    font-family: "Cinzel", serif; font-weight: 500; letter-spacing: 0.3px; white-space: nowrap;
  }
  .card-front .company-name {
    position: absolute; left: 32px; top: 33px; font-size: 21px;
  }
  .holder-name {
    position: absolute; left: 33px; top: 109px;
    font-family: "Roboto Condensed", sans-serif; font-weight: 500; font-size: 21px;
  }
  .holder-title {
    position: absolute; left: 33px; top: 136px;
    font-family: "Roboto", sans-serif; font-size: 14px;
  }
  .address {
    position: absolute; left: 33px; top: 174px;
    font-family: "Roboto", sans-serif; font-size: 14px; line-height: 18px;
  }
  .contact-list {
    position: absolute; left: 33px; top: 220px; list-style: none;
    font-family: "Roboto", sans-serif; font-size: 14px; line-height: 19px;
  }
  .contact-list li { display: flex; align-items: center; gap: 9px; }
  .contact-list svg { width: 13px; height: 13px; fill: var(--ink-white); flex: none; }

  .front-wordmark {
    position: absolute; left: 228px; top: 132px; width: 212px;
    display: flex; flex-direction: column; align-items: center; gap: 14px;
  }
  .front-wordmark .mark-square { width: 30px; height: 30px; background: var(--ink-white); }
  .card-front .front-wordmark .company-name {
    position: static; font-size: 25px; line-height: 30px; color: var(--ink-white);
  }

  /* Back side */
  .card-back { left: 311px; top: 472px; background: var(--paper); text-align: center; }
  .card-back .mark-square {
    position: absolute; left: 262px; top: 70px; width: 76px; height: 76px; background: var(--card-red);
  }
  .card-back .company-name {
    position: absolute; left: 0; right: 0; top: 230px; font-size: 25px; color: var(--ink-grey);
  }
  .card-back .web-address {
    position: absolute; left: 0; right: 0; top: 291px;
    font-family: "Roboto", sans-serif; font-size: 13px; letter-spacing: 5px; color: var(--ink-grey);
  }
</style>
</head>
<body>

<section class="card card-front">
  <div class="side-band"></div>
  <p class="company-name">Brindle Auto Ltd.</p>
  <h1 class="holder-name">MARA QUILL</h1>
  <p class="holder-title">CEO/FOUNDER</p>
  <p class="address">1420 Fenwick Road<br>Halden, Alaska 34012</p>
  <ul class="contact-list">
    <li><svg viewBox="0 0 16 16"><path d="M3.5 1l2.5 3-1.5 1.8c.9 2 2.6 3.7 4.7 4.7L11 9l3 2.5-1.2 2.7C7 13.8 2.2 9 1.8 3.2z"/></svg>555 210 4837</li>
    <li><svg viewBox="0 0 16 16"><path d="M4.5 0h7a1 1 0 0 1 1 1v14a1 1 0 0 1-1 1h-7a1 1 0 0 1-1-1V1a1 1 0 0 1 1-1zm.5 2v10h6V2zm3 11a1 1 0 1 0 0 2 1 1 0 0 0 0-2z"/></svg>555 318 7026</li>
    <li><svg viewBox="0 0 16 16"><path d="M4 1h8v4H4zM1 6h14v7h-3v2H4v-2H1zm4 5v3h6v-3z"/></svg>555 904 6152</li>
    <li><svg viewBox="0 0 16 16"><path d="M1 3h14v10H1zm1.5 1.3V5l5.5 4 5.5-4v-.7L8 8.2z"/></svg>mara@brindle.com</li>
    <li><svg viewBox="0 0 16 16"><path d="M8 1a7 7 0 1 0 0 14A7 7 0 0 0 8 1zm-1 2.2c-.6 1-1.8 1.3-2.3 2.4.8.4 1.7.2 2.2 1 .4.8-.2 1.6.4 2.3.7.7.2 1.8.5 2.8C5.3 11.4 3 9.8 3 8c0-2.2 1.6-4.3 4-4.8zm2.7.3c1.9.6 3.3 2.5 3.3 4.5-.8-.4-1.5-.1-2.1-.8-.5-.7.1-1.6-.5-2.2-.4-.4-1.1-.3-1.2-.9 0-.2.2-.4.5-.6z"/></svg>www.brindle.com</li>
  </ul>
  <div class="front-wordmark">
    <span class="mark-square"></span>
    <span class="company-name">Brindle Auto</span>
  </div>
</section>

<section class="card card-back">
  <span class="mark-square"></span>
  <p class="company-name">Brindle Auto Ltd.</p>
  <p class="web-address">www.brindleauto.com</p>
</section>

</body>
</html>
```